Stylish Business Cards Wanted

- DOUBLE SIDED Design Required -

High end, edgy cards for a corporate and personal stylist. Must include logo,
Name: Belinda Harwick
Title: Director and Stylist
telephone : +61 8 7142 5809
email: belinda@theloombriefing.example
website: theloombriefing.example
Tag: Corporate Workwear & Uniform Specialist | Personal Stylist
Would like nice icons for telephone, email, website

Target Market(s)

Businesses wanting stylish uniforms, people wanting stylish wardrobes

Industry/Entity Type

Corporate Workwear Stylist

Contact Information for Business Card

I would like black, white and gold foiling incorporated in the design - possibly a touch of the other colours on my branding guide attached Name: Belinda Harwick Title: Director and Stylist telephone : +61 8 7142 5809 email: belinda@theloombriefing.example website: theloombriefing.example Tag: Corporate Workwear & Uniform Specialist | Personal Stylist Would like nice icons for telephone, email, website

Font styles to use
Other font styles liked:
• Raleway

Colors

Designer to choose colors to be used in the design.

Requirements
Must have
• Gold foil accents

```html
<!DOCTYPE html>
<html lang="en">
<head>
<meta charset="utf-8">
<title>The Loom Briefing — Business Cards</title>
<link rel="stylesheet" href="https://fonts.googleapis.com/css2?family=Raleway:wght@400;500;600&family=Arimo:wght@400&display=swap">
<style>
  :root {
    --backdrop: #dcdcdc;
    --card: #ffffff;
    --ink: #111111;
    --gold: #e8bf55;
    --muted: #333333;
  }
  * { box-sizing: border-box; margin: 0; padding: 0; }
  html, body { width: 1200px; height: 900px; overflow: hidden; }
  body {
    background: var(--backdrop);
    font-family: "Raleway", sans-serif;
    color: var(--ink);
    display: flex;
    flex-direction: column;
    align-items: center;
    justify-content: center;
    gap: 44px;
  }
  .card {
    position: relative;
    width: 640px;
    height: 366px;
    background: var(--card);
    box-shadow: 0 6px 14px rgba(0,0,0,0.18);
    overflow: hidden;
  }
  .card-band {
    position: absolute;
    left: 0; right: 0; bottom: 0;
    height: 10px;
  }
  .card-band--gold { background: var(--gold); }
  .card-band--black { background: var(--ink); }

  .wordmark {
    display: flex;
    align-items: center;
    gap: 12px;
    font-family: "Raleway", sans-serif;
    font-weight: 600;
    color: var(--ink);
    letter-spacing: 0.12em;
    text-transform: uppercase;
    line-height: 1;
  }
  .wordmark-square {
    width: 22px; height: 22px;
    background: var(--gold);
    flex: none;
  }

  /* Front */
  .card--front .wordmark {
    position: absolute;
    top: 108px;
    left: 0; right: 0;
    justify-content: center;
    font-size: 34px;
  }
  .tagline {
    position: absolute;
    top: 214px;
    left: 0; right: 0;
    text-align: center;
    font-size: 21px;
    font-weight: 500;
    line-height: 1.35;
    letter-spacing: 0.02em;
    text-transform: uppercase;
  }
  .tagline-divider { padding: 0 10px; }

  /* Back */
  .card--back .wordmark {
    position: absolute;
    top: 92px;
    left: 48px;
    font-size: 26px;
  }
  .holder {
    position: absolute;
    top: 42px;
    right: 34px;
    text-align: right;
  }
  .holder-name {
    font-size: 22px;
    font-weight: 600;
    color: var(--gold);
    letter-spacing: 0.01em;
  }
  .holder-title {
    font-size: 12.5px;
    font-weight: 500;
    color: var(--muted);
    margin-top: 2px;
  }
  .holder-tab {
    position: absolute;
    top: 34px;
    right: 0;
    width: 10px;
    height: 56px;
    background: var(--gold);
    border-radius: 6px 0 0 6px;
  }
  .contact-icons {
    position: absolute;
    top: 236px;
    left: 60px;
    display: flex;
    gap: 22px;
  }
  .contact-icon {
    width: 22px; height: 22px;
    border-radius: 50%;
    background: var(--gold);
    display: flex;
    align-items: center;
    justify-content: center;
  }
  .contact-icon svg { width: 13px; height: 13px; }
  .contact-list {
    position: absolute;
    top: 268px;
    left: 60px;
    list-style: none;
    font-family: "Arimo", sans-serif;
    font-size: 15px;
    line-height: 1.4;
    color: var(--ink);
  }
</style>
</head>
<body>

  <section class="card card--front" aria-label="Card front">
    <div class="wordmark"><span class="wordmark-square"></span>The Loom Briefing</div>
    <p class="tagline">
      Corporate Workwear<br>
      Uniform Specialist<span class="tagline-divider">|</span>Personal Stylist
    </p>
    <div class="card-band card-band--gold"></div>
  </section>

  <section class="card card--back" aria-label="Card back">
    <div class="wordmark"><span class="wordmark-square"></span>The Loom Briefing</div>

    <div class="holder">
      <p class="holder-name">Belinda Harwick</p>
      <p class="holder-title">Director and Stylist</p>
    </div>
    <div class="holder-tab"></div>

    <div class="contact-icons">
      <span class="contact-icon" aria-label="Telephone">
        <svg viewBox="0 0 24 24" fill="#111"><path d="M6.6 10.8a15.1 15.1 0 0 0 6.6 6.6l2.2-2.2c.3-.3.7-.4 1-.2 1.1.4 2.3.6 3.6.6.6 0 1 .4 1 1V20c0 .6-.4 1-1 1A17 17 0 0 1 3 4c0-.6.4-1 1-1h3.5c.6 0 1 .4 1 1 0 1.3.2 2.5.6 3.6.1.3 0 .7-.2 1z"/></svg>
      </span>
      <span class="contact-icon" aria-label="Email">
        <svg viewBox="0 0 24 24" fill="none" stroke="#111" stroke-width="2"><rect x="3" y="6" width="18" height="12" rx="1"/><path d="M3 7l9 6 9-6"/></svg>
      </span>
      <span class="contact-icon" aria-label="Website">
        <svg viewBox="0 0 24 24" fill="none" stroke="#111" stroke-width="2"><circle cx="12" cy="12" r="9"/><path d="M3 12h18M12 3c3 3 3 15 0 18M12 3c-3 3-3 15 0 18"/></svg>
      </span>
    </div>

    <ul class="contact-list">
      <li>+61 8 7142 5809</li>
      <li>belinda@theloombriefing.example</li>
      <li>theloombriefing.example</li>
    </ul>

    <div class="card-band card-band--black"></div>
  </section>

</body>
</html>
```